Website to design and sell sundials: www.gnomonvale.com

We have a website that creates a free paper sundial, we want to migrate from this not profit free website to a website where we will continue offering the free paper sundial model but We will also offer a manufactured sundial and sell it.
In order to understand the project, please visit:
http://www.gnomonvale.com/vertical/sundial.html and
http://www.torvel.net/landing/

The website user journey should be redesigned, including the phases that are,
select language
Show product give info
Creation/edit sundial (could be one or more phases)
View created sundial
Buy sundial.

May some of them could be combined or splitted, what It have more sense.

Requirements
Must have
• A description page user journey offering freemium paper sundial and physical sundial to sell.
• A sundial creation page for "free" paper sundial
• A result page for paper sundial
• A sell page for physical

```html
<!DOCTYPE html>
<html lang="en">
<head>
<meta charset="utf-8">
<title>GnomonVale – Create your vertical sundial</title>
<link href="https://fonts.googleapis.com/css2?family=Quicksand:wght@500;700&family=Open+Sans:wght@400;600&display=swap" rel="stylesheet">
<style>
:root{
  --red:#c4100f;
  --red-dark:#a50c0b;
  --text:#555;
  --muted:#777;
  --line:#cfcfcf;
  --footer:#333333;
  --footer-bottom:#2a2a2a;
  --footer-text:#e6e6e6;
  --white:#fff;
}
*{box-sizing:border-box;margin:0;padding:0}
html,body{width:789px;height:1200px;overflow:hidden;background:var(--white)}
body{position:relative;font-family:"Open Sans",sans-serif;color:var(--text);font-size:8px}
.abs{position:absolute}
.top-rule{left:0;top:0;width:789px;height:2px;background:var(--red)}
.brand{left:87px;top:30px;display:flex;align-items:center;gap:8px;font-family:"Quicksand",sans-serif;font-weight:700;font-size:22px;color:var(--red)}
.brand-dot{width:14px;height:14px;border-radius:50%;background:var(--red)}
.lang{left:648px;top:20px;width:54px;height:25px;border:1px solid #ccc;border-radius:2px;box-shadow:0 1px 2px rgba(0,0,0,.15);display:flex;align-items:center;justify-content:center;gap:4px;font-size:7px;color:#444}
.lang-dot{width:10px;height:10px;border-radius:50%;background:#2b3f8c}
.nav{top:68px;left:408px;display:flex;font-family:"Quicksand",sans-serif;font-weight:500;font-size:8px;color:#333;letter-spacing:.5px}
.nav span{margin-right:31px;position:relative;height:26px}
.nav .active{color:var(--red)}
.nav .active::after{content:"";position:absolute;left:0;right:0;bottom:0;height:2px;background:var(--red)}
.hero{left:0;top:94px;width:789px;height:173px;background:linear-gradient(90deg,#2f3522 0%,#5a5d4c 35%,#8c8b86 55%,#4b5136 100%)}
.hero h1{position:absolute;left:0;right:0;top:64px;text-align:center;font-family:"Quicksand",sans-serif;font-weight:700;font-size:28px;color:var(--white)}
h2{position:absolute;font-family:"Quicksand",sans-serif;font-weight:700;font-size:20px;color:var(--red)}
.intro{left:88px;top:325px;width:370px;font-size:7.2px;line-height:13px;color:#555}
.field{border:1px solid var(--line);background:var(--white)}
.search-input{left:87px;top:370px;width:252px;height:25px;font-size:7.2px;color:#777;padding:8px 8px}
.btn{background:var(--red);color:var(--white);border-radius:2px;font-size:7.5px;display:flex;align-items:center;justify-content:center}
.search-btn{left:349px;top:369px;width:43px;height:26px}
.label{font-size:7.2px;color:#555}
.small-field{width:52px;height:20px}
.map{left:479px;top:296px;width:223px;height:217px;background:linear-gradient(135deg,#2c4f8f 0%,#1b3366 45%,#6d7b4f 70%,#b49a62 100%);border:2px solid var(--white);box-shadow:0 0 3px rgba(0,0,0,.3)}
.option-photo{width:140px;height:93px;border:3px solid var(--white);box-shadow:0 0 3px rgba(0,0,0,.3)}
.photo-a{left:87px;top:587px;background:linear-gradient(90deg,#4a4a4a 0%,#e6ecef 25%,#e8e8e8 55%,#9c5a44 80%,#a4604a 100%)}
.photo-b{left:249px;top:587px;background:linear-gradient(90deg,#1f1f1f 0%,#3a3a2e 25%,#cfc1ae 45%,#a99a88 70%,#c7cfd3 100%)}
.option-title{font-family:"Quicksand",sans-serif;font-weight:500;font-size:13px;color:var(--red);width:140px;text-align:center}
.radio{width:12px;height:12px;border-radius:50%;border:1px solid #ccc;background:var(--white)}
.radio.on::after{content:"";position:absolute;left:3px;top:3px;width:4px;height:4px;border-radius:50%;background:#222}
.check{width:12px;height:12px;border:1px solid #ccc;background:#fafafa}
.select{left:129px;top:839px;width:137px;height:20px;font-size:7.2px;color:#444;padding:5px 8px;display:flex;justify-content:space-between}
.create-btn{left:87px;top:918px;width:67px;height:21px}
.footer{left:0;top:976px;width:789px;height:182px;background:var(--footer);border-top:3px solid var(--red)}
.footer-bottom{left:0;top:1158px;width:789px;height:42px;background:var(--footer-bottom);color:var(--footer-text);font-size:7.2px;text-align:center;line-height:42px}
.footer h3{position:absolute;font-family:"Quicksand",sans-serif;font-weight:700;font-size:12.5px;color:var(--white)}
.links{color:var(--footer-text);font-size:6.6px;line-height:12.6px}
.contact-row{display:flex;gap:9px;align-items:flex-start;color:var(--footer-text);font-size:6.6px;line-height:9px;width:140px}
.contact-row svg{flex:none;margin-top:1px}
.news-text{left:387px;top:1038px;color:var(--footer-text);font-size:6.6px}
.news-input{left:387px;top:1057px;width:129px;height:23px;background:#5c5c5c;color:#ddd;font-size:6.6px;padding:7px 8px}
.subscribe{left:387px;top:1089px;width:55px;height:17px;font-size:7px}
.footer-brand{left:546px;top:1010px;display:flex;align-items:center;gap:6px;font-family:"Quicksand",sans-serif;font-weight:700;font-size:14px;color:#aaa}
.footer-brand .dot{width:10px;height:10px;border-radius:50%;background:#aaa}
.social{left:600px;top:1046px;display:flex;gap:4px}
.social span{width:23px;height:23px;border:1.5px solid var(--white);border-radius:50%}
</style>
</head>
<body>
<div class="abs top-rule"></div>

<header>
  <div class="abs brand"><span class="brand-dot"></span>GnomonVale.com</div>
  <div class="abs lang"><span class="lang-dot"></span>ENG
    <svg width="6" height="4" viewBox="0 0 6 4"><path d="M0.5 0.5 3 3 5.5 0.5" fill="none" stroke="#444"/></svg>
  </div>
  <nav class="abs nav">
    <span>Home</span><span>About Us</span><span class="active">Product</span><span>Creation</span><span>Contact us</span>
  </nav>
</header>

<section class="abs hero" role="img" aria-label="Photo of a paper vertical sundial lying on grass">
  <h1>Create your vertical sundial</h1>
</section>

<section class="location">
  <h2 style="left:85px;top:290px">Sundial location</h2>
  <p class="abs intro">Select the location where you want to place your paper sundial, mark a line along building wall where you want to put it. Write your address and press Go! (e.g. Picadilly circus, london, UK)</p>
  <div class="abs field search-input">Enter Your Keyword</div>
  <div class="abs btn search-btn">Search</div>
  <span class="abs label" style="left:88px;top:418px">Longitude</span>
  <div class="abs field small-field" style="left:133px;top:413px"></div>
  <span class="abs label" style="left:193px;top:418px">Latitude:</span>
  <div class="abs field small-field" style="left:232px;top:413px"></div>
  <span class="abs label" style="left:293px;top:418px">Wall declination:</span>
  <div class="abs field small-field" style="left:353px;top:413px"></div>
  <span class="abs label" style="left:87px;top:457px">Now select the face of the building</span>
  <div class="abs map" role="img" aria-label="Satellite map for picking the sundial location"></div>
</section>

<section class="options">
  <h2 style="left:86px;top:538px">Sundial options</h2>
  <div class="abs option-photo photo-a" role="img" aria-label="Paper sundial fixed on a brick wall"></div>
  <div class="abs option-photo photo-b" role="img" aria-label="Paper sundial on a balcony wall"></div>
  <div class="abs option-title" style="left:87px;top:692px">Wall sundial</div>
  <div class="abs option-title" style="left:249px;top:692px">Wall sundial</div>
  <div class="abs radio on" style="left:151px;top:715px"></div>
  <div class="abs radio" style="left:313px;top:715px"></div>

  <span class="abs label" style="left:87px;top:750px">Banner:</span>
  <div class="abs field" style="left:124px;top:744px;width:94px;height:20px;font-size:7.2px;padding:5px 8px">Paper sundial</div>
  <span class="abs label" style="left:87px;top:781px">Solar Time:</span>
  <div class="abs radio" style="left:133px;top:779px"></div>
  <span class="abs label" style="left:155px;top:781px">Civil Time:</span>
  <div class="abs radio" style="left:201px;top:779px"></div>
  <span class="abs label" style="left:87px;top:808px">Daylight Saving Time:</span>
  <div class="abs check" style="left:168px;top:806px"></div>
  <span class="abs label" style="left:87px;top:845px">Timezone</span>
  <div class="abs field select"><span>(GMT-12)&nbsp;&nbsp;&nbsp;Eniwetok, Kwajalein</span>
    <svg width="6" height="8" viewBox="0 0 6 8"><path d="M0 2h6L3 5z" fill="#444"/></svg>
  </div>
  <span class="abs label" style="left:87px;top:882px">Equation of time</span>
  <div class="abs check" style="left:152px;top:878px"></div>
  <div class="abs btn create-btn">Creat Sundial</div>
</section>

<footer class="abs footer">
  <h3 style="left:86px;top:25px">Quick Links</h3>
  <div class="abs links" style="left:88px;top:57px">Home<br>About Us<br>product<br>Creation<br>Contact us</div>

  <h3 style="left:217px;top:25px">Contact us</h3>
  <div class="abs contact-row" style="left:218px;top:59px">
    <svg width="8" height="7" viewBox="0 0 8 7"><path d="M0 2Q4-1 8 2V3H6V2H2V3H0zM1 4H7V7H1z" fill="#fff"/></svg>(555) 014-3129</div>
  <div class="abs contact-row" style="left:218px;top:76px">
    <svg width="8" height="7" viewBox="0 0 8 7"><path d="M2 0H6V2H8V6H6V7H2V6H0V2H2z" fill="#fff"/></svg>(555) 014-4633</div>
  <div class="abs contact-row" style="left:218px;top:94px">
    <svg width="8" height="6" viewBox="0 0 8 6"><rect width="8" height="6" fill="#fff"/><path d="M0 0 4 3.5 8 0" fill="none" stroke="#333"/></svg><span style="text-decoration:underline">hello@gnomonvale.com</span></div>
  <div class="abs contact-row" style="left:218px;top:112px">
    <svg width="6" height="9" viewBox="0 0 6 9"><path d="M3 0A3 3 0 0 1 6 3C6 5 3 9 3 9S0 5 0 3A3 3 0 0 1 3 0z" fill="#fff"/><circle cx="3" cy="3" r="1.1" fill="#333"/></svg>#2868 Lorem ipsum dolor sit amet, consectetur adipiscing elit</div>

  <h3 style="left:387px;top:23px">Newsletter</h3>
  <div class="abs footer-brand"><span class="dot"></span>GnomonVale.com</div>
  <div class="abs social"><span></span><span></span><span></span><span></span></div>
</footer>
<div class="abs news-text">Sign Up for Our Newsletter &amp; Promotion</div>
<div class="abs news-input">Enter Your email Id</div>
<div class="abs btn subscribe">SUBSCRIBE</div>

<div class="abs footer-bottom">© 2016 gnomonvale.com&nbsp; All Rights Reserved</div>
</body>
</html>
```